Develop website for Cloud Security Startup

Looking for a logo that conveys the outsourced security and management of clients data, systems and development in Tellix, Bri and Pindle with an emphasis on security and compliance

Target Market(s)

Companies looking for professional services IT firm

Coding

Coded - Design and coding required

Number of Pages Required

5+ page

Font styles to use
Sans Serif

Colors
0455a3
33a6d7

Requirements
Must have
• Landing Page
- Help me get started

Move to the cloud safely
- Benefits of Cloud

What we do
- Cloud Adoption
- Managed Services
- Optimise

Resources
- News
- Resources
- Events
- Webinars
- Not for profit
- Case Studies
- Support Button
- Incident Button

Company
- About Us
- Why Vorplexa?
- Acreditations
- Quorvane Tellix Partner
- Net Promoter Score
- Careers
- Contact Us

Contact Us

```html
<!DOCTYPE html>
<html lang="en">
<head>
<meta charset="utf-8">
<title>Vorplexa – Effective Technology Management</title>
<link href="https://fonts.googleapis.com/css2?family=Montserrat:wght@400;500;600;700;800&family=Open+Sans:wght@400;600;700&display=swap" rel="stylesheet">
<style>
:root{
  --brand:#0455a3;
  --accent:#33a6d7;
  --navy:#06204a;
  --night:#041226;
  --ink:#1c1c1c;
  --muted:#555a66;
  --tint:#eef0f8;
  --line:#c9ccd8;
  --white:#ffffff;
}
*{box-sizing:border-box;margin:0;padding:0}
html,body{width:1200px;height:4835px;overflow:hidden}
body{position:relative;background:var(--white);font-family:"Open Sans",sans-serif;color:var(--ink)}
.abs{position:absolute}
.head{font-family:"Montserrat",sans-serif}

/* header */
.topbar{left:0;top:0;width:1200px;height:66px;background:linear-gradient(90deg,var(--brand),var(--accent))}
.topbar p{position:absolute;left:360px;top:25px;color:var(--white);font:700 12px "Open Sans",sans-serif}
.navbar{left:0;top:66px;width:1200px;height:79px;background:var(--white);border-bottom:3px solid var(--brand)}
.brand-tab{left:118px;top:0;width:214px;height:145px;background:var(--white);border-radius:107px 107px 0 0}
.brand-tab .dot{position:absolute;left:82px;top:10px;width:50px;height:50px;border-radius:50%;background:var(--brand)}
.brand-tab .name{position:absolute;left:0;width:214px;top:94px;text-align:center;font:700 28px "Montserrat",sans-serif;color:var(--brand);letter-spacing:1px}
.nav a{position:absolute;top:100px;font:600 12.5px "Montserrat",sans-serif;color:var(--ink);text-decoration:none}
.nav a.active{color:var(--brand)}
.nav .pin{position:absolute;left:401px;top:80px;width:12px;height:12px;border-radius:50%;background:var(--brand)}
.call{left:886px;top:80px;width:50px;height:50px;border-radius:50%;background:linear-gradient(135deg,var(--accent),var(--brand))}
.call-label{left:948px;top:86px;font:600 12px "Montserrat",sans-serif}
.call-num{left:948px;top:104px;font:700 22px "Montserrat",sans-serif;color:var(--brand)}

/* hero */
.hero{left:0;top:145px;width:1200px;height:625px;overflow:hidden;background:radial-gradient(ellipse 420px 300px at 600px 300px,#1c4f86 0%,#0c2a52 45%,#041226 100%)}
.hero h1{position:absolute;left:0;width:1200px;top:176px;text-align:center;color:var(--white);font:700 44px "Montserrat",sans-serif;letter-spacing:.5px}
.hero .mark{position:absolute;left:578px;top:118px;width:44px;height:44px;border-radius:50%;background:var(--white)}
.hero .lede{position:absolute;left:0;width:1200px;top:248px;text-align:center;color:var(--white);font:400 14px/30px "Open Sans",sans-serif}
.btn{position:absolute;left:505px;top:340px;width:190px;height:56px;border-radius:28px;background:linear-gradient(180deg,var(--accent),var(--brand));color:var(--white);font:700 15px/56px "Montserrat",sans-serif;text-align:center}
.dots{left:570px;top:696px;display:flex;gap:5px}
.dots i{width:9px;height:9px;border-radius:50%;background:#dfe3ec;display:block}
.dots i.on{background:var(--accent)}

/* section titles */
.title{left:0;width:1200px;text-align:center;font:400 34px "Montserrat",sans-serif;color:var(--accent)}
.title b{color:var(--brand);font-weight:700}
.title-dot{width:18px;height:18px;border-radius:50%;background:var(--brand);left:591px}
.intro{left:150px;width:900px;text-align:center;font:400 11.5px/30px "Open Sans",sans-serif;color:var(--ink)}

/* about */
.badge{width:210px;height:210px;border-radius:50%;background:linear-gradient(135deg,var(--brand),var(--accent))}
.badge-label{width:300px;text-align:center;font:700 16px "Montserrat",sans-serif;color:var(--ink)}

/* what we do */
.band{left:0;top:1343px;width:1200px;height:1239px;background:var(--tint)}
.service h3{font:700 21px "Montserrat",sans-serif;color:var(--brand)}
.service h4{margin-top:20px;font:700 17px/30px "Montserrat",sans-serif;color:var(--accent)}
.service p{margin-top:12px;font:400 12.5px/30px "Open Sans",sans-serif;color:var(--ink)}
.service{width:450px}
.illus{border-radius:24px;background:linear-gradient(135deg,#cfe4f5,#9cc9ea)}

/* benefits */
.benefit{font:400 14px/30px "Open Sans",sans-serif;color:var(--muted)}
.benefit.r{text-align:right}
.benefit.c{text-align:center;width:300px}
.core-name{left:496px;top:3168px;width:210px;text-align:center;font:700 30px "Montserrat",sans-serif;color:var(--brand)}

/* resources */
.card{width:475px;height:196px;background:var(--white);box-shadow:0 6px 18px rgba(20,40,80,.14);display:flex}
.card .thumb{width:191px;height:196px}
.card .body{padding:22px 0 0 15px;width:284px}
.card h3{font:700 16px "Montserrat",sans-serif;color:var(--brand)}
.card .date{margin-top:8px;font:500 11px "Montserrat",sans-serif;color:var(--accent)}
.card p{margin-top:8px;font:400 11px/24px "Open Sans",sans-serif;color:var(--ink)}
.card .meta{margin-top:4px;display:flex;gap:58px;font:700 11px "Montserrat",sans-serif;color:var(--brand)}
.card .meta span+span{color:#999;font-weight:600;font-size:9.5px}

/* footer */
.foot{left:0;top:4130px;width:1200px;height:705px}
.foot-bg{left:0;top:4130px;width:1200px;height:705px;background:linear-gradient(180deg,#0a2444,#020a16)}
.mail-title{left:0;width:1200px;top:4352px;text-align:center;color:var(--white);font:700 32px "Montserrat",sans-serif}
.mail-text{left:0;width:1200px;top:4410px;text-align:center;color:var(--white);font:400 12px "Open Sans",sans-serif}
.field{left:244px;top:4455px;width:641px;height:48px;border-radius:24px;background:var(--white);border:2px solid var(--accent)}
.field span{position:absolute;left:45px;top:15px;font:400 11px "Open Sans",sans-serif;color:#9aa}
.submit{left:745px;top:4455px;width:140px;height:48px;border-radius:24px;background:linear-gradient(180deg,var(--accent),var(--brand));color:var(--white);font:700 17px/48px "Montserrat",sans-serif;text-align:center}
.rule{left:90px;width:1018px;height:1px;background:rgba(255,255,255,.35)}
.col h5{font:700 17px "Montserrat",sans-serif;color:var(--white);letter-spacing:.5px}
.col ul{list-style:none;margin-top:14px}
.col li{font:400 13px/30px "Open Sans",sans-serif;color:var(--white)}
.col li::before{content:"»";margin-right:10px}
.col.contact li::before{content:none}
.col.contact li{display:flex;gap:14px;align-items:flex-start}
.col.contact svg{flex:none;margin-top:9px}
.foot-mark{left:166px;top:4578px;width:44px;height:44px;border-radius:50%;background:var(--white)}
.foot-name{left:88px;top:4648px;width:200px;text-align:center;font:700 22px "Montserrat",sans-serif;color:var(--white)}
.social{top:4695px;width:30px;height:30px;border-radius:50%;background:var(--white)}
.copy{left:90px;top:4788px;font:400 12px "Open Sans",sans-serif;color:var(--white)}
</style>
</head>
<body>

<!-- Header -->
<div class="abs topbar"><p>Lorem ipsum dolor sit amet, consectetur adipiscing elit, sed do eiusmod tempor incididunt ut labore et dolore</p></div>
<div class="abs navbar"></div>
<div class="abs brand-tab"><span class="dot"></span><span class="name">VORPLEXA</span></div>
<nav class="nav">
  <span class="abs pin"></span>
  <a class="active" style="left:390px">HOME</a>
  <a style="left:456px">COMPANY</a>
  <a style="left:546px">WHAT WE DO</a>
  <a style="left:659px">RESOURCES</a>
  <a style="left:764px">CONTACT US</a>
</nav>
<div class="abs call">
  <svg width="50" height="50" viewBox="0 0 50 50"><path d="M19 16c2-1 3 0 4 3l1 3c0 1-1 2-2 3 1 3 3 5 6 6 1-1 2-2 3-2l3 1c3 1 4 2 3 4-1 3-3 4-6 3-7-2-12-7-14-14-1-3 0-5 2-7z" fill="#fff"/></svg>
</div>
<div class="abs call-label">Call Us Today</div>
<div class="abs call-num">123 456 7890</div>

<!-- Hero -->
<section class="abs hero" role="img" aria-label="Dark blue digital globe surrounded by network device icons">
  <span class="mark"></span>
  <h1>EFFECTIVE TECHNOLOGY MANAGEMENT</h1>
  <p class="lede">Lorem ipsum dolor sit amet, consectetur adipiscing elit, sed do eiusmod tempor incididunt ut labore et dolore magna aliqua.<br>Ut enim ad minim veniam, quis nostrud exercitation ullamco laboris nisi ut aliquip ex ea commodo consequat.</p>
  <div class="btn">GET STARTED</div>
  <svg class="abs" style="left:0;top:0" width="1200" height="625" viewBox="0 0 1200 625">
    <path d="M0 470 Q600 760 1200 470 V625 H0 Z" fill="#fff"/>
    <path d="M0 462 Q600 752 1200 462" fill="none" stroke="#0455a3" stroke-width="6"/>
  </svg>
</section>
<div class="abs dots"><i></i><i class="on"></i><i></i><i></i><i></i></div>

<!-- About -->
<span class="abs title-dot" style="top:842px"></span>
<h2 class="abs title" style="top:866px">ABOUT <b>VORPLEXA</b></h2>
<p class="abs intro" style="top:912px">Lorem ipsum dolor sit amet, consectetur adipiscing elit, sed do eiusmod tempor incididunt ut labore et dolore magna aliqua. Quis ipsum suspendisse ultrices gravida. Risus commodo viverra maecenas accumsan lacus vel facilisis.</p>
<div class="abs badge" style="left:207px;top:1018px" role="img" aria-label="Question mark icon"></div>
<div class="abs badge" style="left:495px;top:1018px" role="img" aria-label="Person climbing a growth arrow icon"></div>
<div class="abs badge" style="left:783px;top:1018px" role="img" aria-label="Cloud connected to people icon"></div>
<div class="abs badge-label" style="left:145px;top:1237px">WHY VORPLEXA?</div>
<div class="abs badge-label" style="left:433px;top:1237px">CAREERS</div>
<div class="abs badge-label" style="left:721px;top:1237px">QUORVANE TELLIX PARTNER</div>

<!-- What we do -->
<div class="abs band"></div>
<span class="abs title-dot" style="top:1430px"></span>
<h2 class="abs title" style="top:1454px">WHAT <b>WE DO</b></h2>
<svg class="abs" style="left:0;top:0" width="1200" height="2600" viewBox="0 0 1200 2600">
  <path d="M565 1540 Q531 1540 531 1575 V1800 Q531 1855 572 1855 Q614 1855 614 1900 V2140 Q614 2180 572 2180 Q531 2180 531 2225 V2455 Q531 2490 565 2490" fill="none" stroke="#c9ccd8" stroke-width="3"/>
</svg>
<div class="abs illus" style="left:222px;top:1568px;width:219px;height:225px" role="img" aria-label="Cloud with circuit lines icon"></div>
<div class="abs illus" style="left:695px;top:1897px;width:220px;height:225px" role="img" aria-label="Cloud with screwdriver and wrench icon"></div>
<div class="abs illus" style="left:225px;top:2263px;width:216px;height:200px" role="img" aria-label="Gears and bar chart icon"></div>

<div class="abs service" style="left:599px;top:1547px">
  <h3>CLOUD ADOPTION</h3>
  <h4>Lorem ipsum dolor sit amet, consectetur adipisc-ing elit, sed do eiusmod tempor incididunt</h4>
  <p>Lorem ipsum dolor sit amet, consectetur adipiscing elit, sed do eius-mod tempor incididunt ut labore et dolore magna aliqua. Ut enim ad minim veniam, quis nostrud exercitation ullamco laboris nisi ut aliquip ex ea commodo consequat. Duis aute irure dolor in reprehenderit in voluptate velit esse cillum dolore eu fugiat nulla pariatur.</p>
</div>
<div class="abs service" style="left:137px;top:1881px">
  <h3>MANAGED SERVICES</h3>
  <h4>Lorem ipsum dolor sit amet, consectetur adipisc-ing elit, sed do eiusmod tempor incididunt</h4>
  <p>Lorem ipsum dolor sit amet, consectetur adipiscing elit, sed do eius-mod tempor incididunt ut labore et dolore magna aliqua. Ut enim ad minim veniam, quis nostrud exercitation ullamco laboris nisi ut aliquip ex ea commodo consequat. Duis aute irure dolor in reprehenderit in voluptate velit esse cillum dolore eu fugiat nulla pariatur.</p>
</div>
<div class="abs service" style="left:599px;top:2232px">
  <h3>OPTIMISE</h3>
  <h4>Lorem ipsum dolor sit amet, consectetur adipisc-ing elit, sed do eiusmod tempor incididunt</h4>
  <p>Lorem ipsum dolor sit amet, consectetur adipiscing elit, sed do eius-mod tempor incididunt ut labore et dolore magna aliqua. Ut enim ad minim veniam, quis nostrud exercitation ullamco laboris nisi ut aliquip ex ea commodo consequat. Duis aute irure dolor in reprehenderit in voluptate velit esse cillum dolore eu fugiat nulla pariatur.</p>
</div>

<!-- Benefits -->
<span class="abs title-dot" style="top:2672px"></span>
<h2 class="abs title" style="top:2696px">BENEFITS <b>OF CLOUD</b></h2>
<p class="abs intro" style="top:2741px">Lorem ipsum dolor sit amet, consectetur adipiscing elit, sed do eiusmod tempor incididunt ut labore et dolore magna aliqua. Quis ipsum suspendisse ultrices gravida. Risus commodo viverra maecenas accumsan lacus vel facilisis.</p>
<svg class="abs" style="left:0;top:2850px" width="1200" height="600" viewBox="0 2850 1200 600">
  <circle cx="601" cy="3155" r="205" fill="none" stroke="#eef0f8" stroke-width="10"/>
  <circle cx="601" cy="3155" r="150" fill="#fff" stroke="#eef0f8" stroke-width="4"/>
  <circle cx="601" cy="3122" r="34" fill="#0455a3"/>
  <g fill="#0455a3">
    <circle cx="597" cy="2949" r="8"/><circle cx="447" cy="3020" r="8"/>
    <circle cx="396" cy="3153" r="8"/><circle cx="445" cy="3292" r="8"/>
    <circle cx="597" cy="3360" r="8"/><circle cx="753" cy="3016" r="8"/>
    <circle cx="809" cy="3153" r="8"/><circle cx="753" cy="3294" r="8"/>
  </g>
  <g fill="none" stroke="#6b7280" stroke-width="2">
    <circle cx="597" cy="2907" r="18"/><circle cx="391" cy="3018" r="18"/>
    <circle cx="340" cy="3151" r="18"/><circle cx="391" cy="3288" r="18"/>
    <circle cx="597" cy="3409" r="18"/><circle cx="808" cy="3014" r="18"/>
    <circle cx="862" cy="3151" r="18"/><circle cx="808" cy="3291" r="18"/>
  </g>
</svg>
<div class="abs core-name">VORPLEXA</div>
<p class="abs benefit c" style="left:447px;top:2818px">Lorem ipsum dolor sit amet<br>sed do eiusmod tempor incididunt ut</p>
<p class="abs benefit r" style="left:57px;top:2993px;width:300px">Lorem ipsum dolor sit amet<br>sed do eiusmod tempor incididunt ut</p>
<p class="abs benefit r" style="left:4px;top:3124px;width:300px">Lorem ipsum dolor sit amet<br>sed do eiusmod tempor incididunt ut</p>
<p class="abs benefit r" style="left:57px;top:3263px;width:300px">Lorem ipsum dolor sit amet<br>sed do eiusmod tempor incididunt ut</p>
<p class="abs benefit c" style="left:447px;top:3436px">Lorem ipsum dolor sit amet<br>sed do eiusmod tempor incididunt ut</p>
<p class="abs benefit" style="left:858px;top:2989px">Lorem ipsum dolor sit amet<br>sed do eiusmod tempor incididunt ut</p>
<p class="abs benefit" style="left:898px;top:3124px">Lorem ipsum dolor sit amet<br>sed do eiusmod tempor incididunt ut</p>
<p class="abs benefit" style="left:858px;top:3265px">Lorem ipsum dolor sit amet<br>sed do eiusmod tempor incididunt ut</p>

<!-- Resources -->
<span class="abs title-dot" style="top:3652px"></span>
<h2 class="abs title" style="top:3676px">OUR <b>RESOURCES</b></h2>

<article class="abs card" style="left:111px;top:3748px">
  <div class="thumb" role="img" aria-label="Hand touching a glowing digital screen" style="background:linear-gradient(135deg,#c9d3e0,#2c3e5a)"></div>
  <div class="body"><h3>LOREM IPSUM DOLOR SIT</h3><div class="date">MAY 25 2021</div><p>Lorem ipsum dolor sit amet, consectetur adipiscing elit, sed do eiusmod tempor incididunt ut labore et.</p><div class="meta"><span>LEARN MORE</span><span>15 COMMENT</span></div></div>
</article>
<article class="abs card" style="left:614px;top:3748px">
  <div class="thumb" role="img" aria-label="Hands typing on a laptop with a security overlay" style="background:linear-gradient(135deg,#1b3d6e,#0b1626)"></div>
  <div class="body"><h3>LOREM IPSUM DOLOR SIT</h3><div class="date">MAY 25 2021</div><p>Lorem ipsum dolor sit amet, consectetur adipiscing elit, sed do eiusmod tempor incididunt ut labore et.</p><div class="meta"><span>LEARN MORE</span><span>15 COMMENT</span></div></div>
</article>
<article class="abs card" style="left:111px;top:3978px">
  <div class="thumb" role="img" aria-label="Glowing cloud security illustration in blue and red" style="background:linear-gradient(135deg,#0f6a8c,#0a1a33 60%,#5a1a2a)"></div>
  <div class="body"><h3>LOREM IPSUM DOLOR SIT</h3><div class="date">MAY 25 2021</div><p>Lorem ipsum dolor sit amet, consectetur adipiscing elit, sed do eiusmod tempor incididunt ut labore et.</p><div class="meta"><span>LEARN MORE</span><span>15 COMMENT</span></div></div>
</article>
<article class="abs card" style="left:614px;top:3978px">
  <div class="thumb" role="img" aria-label="Server room aisle lit in blue" style="background:linear-gradient(180deg,#2a3f8a,#0c1440)"></div>
  <div class="body"><h3>LOREM IPSUM DOLOR SIT</h3><div class="date">MAY 25 2021</div><p>Lorem ipsum dolor sit amet, consectetur adipiscing elit, sed do eiusmod tempor incididunt ut labore et.</p><div class="meta"><span>LEARN MORE</span><span>15 COMMENT</span></div></div>
</article>

<!-- Footer -->
<div class="abs foot-bg"></div>
<svg class="abs" style="left:0;top:4130px" width="1200" height="300" viewBox="0 4130 1200 300">
  <path d="M0 4130 H1200 V4412 Q600 4120 0 4412 Z" fill="#fff"/>
  <path d="M0 4412 Q600 4120 1200 4412" fill="none" stroke="#0455a3" stroke-width="6"/>
</svg>
<h2 class="abs mail-title">JOIN OUR MAILING LIST</h2>
<p class="abs mail-text">Lorem ipsum dolor sit amet, consectetur adipiscing elit, sed do eiusmod tempor</p>
<div class="abs field"><span>Enter Email Here</span></div>
<div class="abs submit">SUBMIT</div>
<div class="abs rule" style="top:4541px"></div>

<span class="abs foot-mark"></span>
<div class="abs foot-name">VORPLEXA</div>
<span class="abs social" style="left:92px"></span>
<span class="abs social" style="left:139px"></span>
<span class="abs social" style="left:186px"></span>
<span class="abs social" style="left:233px"></span>

<div class="abs col" style="left:360px;top:4574px">
  <h5>QUICK LINKS</h5>
  <ul><li>Home</li><li>Company</li><li>What We Do</li><li>Resources</li><li>Contact Us</li></ul>
</div>
<div class="abs col" style="left:612px;top:4574px">
  <h5>LEGAL</h5>
  <ul><li>Terms of Use</li><li>Privacy Policy</li><li>Contact Us</li><li>FAQ</li></ul>
</div>
<div class="abs col contact" style="left:832px;top:4574px">
  <h5>CONTACT US</h5>
  <ul>
    <li><svg width="12" height="14" viewBox="0 0 12 14"><path d="M6 0a5 5 0 0 1 5 5c0 4-5 9-5 9S1 9 1 5a5 5 0 0 1 5-5z" fill="#fff"/><circle cx="6" cy="5" r="2" fill="#0a2444"/></svg><span>123 Lorem ipsum dolor sit amet,<br>consectetur adipiscing elit</span></li>
    <li style="margin-top:6px"><svg width="12" height="12" viewBox="0 0 12 12"><path d="M2 1c1 0 2 2 2 3L3 5c1 2 2 3 4 4l1-1c1 0 3 1 3 2s-1 2-2 2C5 12 0 7 0 3 0 2 1 1 2 1z" fill="#fff"/></svg><span>123 456 7890</span></li>
    <li style="margin-top:6px"><svg width="13" height="10" viewBox="0 0 13 10"><rect width="13" height="10" rx="1" fill="#fff"/><path d="M0 1l6.5 5L13 1" fill="none" stroke="#0a2444" stroke-width="1.3"/></svg><span>hello@vorplexa-mail.com</span></li>
  </ul>
</div>
<div class="abs rule" style="top:4770px"></div>
<p class="abs copy">© Copyrights 2021 VORPLEXA &nbsp; | &nbsp; All Rights Reserved</p>

</body>
</html>
```